Jewelers Website

This is for the DESIGN ONLY.
I am a software programmer and will be doing the development.
New website design for
www.lunacrestgems.com.au
Need a fresh new look for an online only jewellery business who produce their jewellery by hand. I would like it designed in a parallax style. Feel free to recommend fonts to use for the site. This is an Australian based company located in NSW so shots of sites in NSW might make nice background images.
http://vornaplex.me/demo/#theme=parallax
To contain the below sections
About Us
Contact Us
Gallery
Testimonials
Diamond Types
The colour scheme is to be Black / White and Silver.
With the Parallax style there will be moving sections and images for added impact.
Target Market(s)
Young Adults mainly engagement jewellery

```html
<!DOCTYPE html>
<html lang="en">
<head>
<meta charset="utf-8">
<title>Lunacrest Gems — Diamond Engagement Rings &amp; Jewellery</title>
<link href="https://fonts.googleapis.com/css2?family=Open+Sans:wght@400;600&family=Didact+Gothic&family=Tinos:wght@400;700&display=swap" rel="stylesheet">
<style>
  :root {
    --nav-bg: #2a2a2a;
    --ink: #222222;
    --body-text: #555555;
    --white: #ffffff;
    --dark-band: #0e0e0e;
    --dark-band-2: #2a2a2a;
    --accent-red: #e0131b;
    --pink: #ee5fae;
    --blue: #1e73be;
    --silver: #c9ccd1;
    --contact-a: #5f84a8;
    --contact-b: #8eaecb;
    --footer-bg: #1c1c1c;
  }
  * { box-sizing: border-box; margin: 0; padding: 0; }
  html, body { width: 1200px; height: 2500px; overflow: hidden; }
  body { position: relative; background: var(--white); font-family: 'Open Sans', sans-serif; color: var(--ink); }

  .site-nav { position: absolute; left: 0; top: 0; width: 1200px; height: 84px; background: var(--nav-bg); }
  .nav-link { position: absolute; top: 36px; font-family: 'Open Sans', sans-serif; font-size: 14px; color: var(--white); transform: translateX(-50%); white-space: nowrap; }
  .brand { position: absolute; left: 593px; top: 14px; transform: translateX(-50%); text-align: center; font-family: 'Tinos', serif; font-size: 25px; line-height: 26px; letter-spacing: 1px; color: var(--white); text-transform: uppercase; }

  .hero { position: absolute; left: 0; top: 84px; width: 1200px; height: 476px; background: linear-gradient(180deg, #7d8ea3 0%, #5e6f73 28%, #3f4a34 55%, #6b5a3f 80%, #3d3a2c 100%); }
  .hero-title { position: absolute; left: 0; width: 1200px; top: 210px; text-align: center; font-family: 'Didact Gothic', sans-serif; font-size: 37px; color: var(--white); }
  .hero-arrow { position: absolute; top: 218px; }
  .hero-dots { position: absolute; left: 560px; top: 534px; }

  .about { position: absolute; left: 0; top: 560px; width: 1200px; height: 318px; background: var(--white); }
  .section-title { font-family: 'Didact Gothic', sans-serif; font-size: 31px; font-weight: 400; }
  .about .section-title { position: absolute; left: 100px; top: 24px; color: var(--ink); }
  .about-copy { position: absolute; left: 100px; top: 78px; width: 660px; font-size: 12.3px; line-height: 25px; color: var(--body-text); }
  .about-copy p { margin-bottom: 2px; }
  .about-photo { position: absolute; left: 773px; top: 70px; width: 327px; height: 200px; background: linear-gradient(135deg, #5b3a1c 0%, #b5541c 35%, #2d2a24 60%, #d8d8d8 100%); }

  .diamond-types { position: absolute; left: 0; top: 878px; width: 1200px; height: 359px; background: radial-gradient(ellipse at 50% 40%, var(--dark-band-2) 0%, var(--dark-band) 75%); color: var(--white); text-align: center; }
  .diamond-types .section-title { position: absolute; left: 0; width: 1200px; top: 26px; }
  .type-card { position: absolute; top: 90px; width: 320px; transform: translateX(-50%); }
  .type-icon { display: block; margin: 0 auto; }
  .type-name { font-family: 'Didact Gothic', sans-serif; font-size: 25px; font-weight: 400; margin-top: 14px; }
  .type-text { font-size: 11.5px; line-height: 21px; margin-top: 10px; }
  .type-more { font-size: 12px; color: var(--accent-red); margin-top: 10px; }

  .gallery { position: absolute; left: 0; top: 1237px; width: 1200px; height: 431px; background: var(--white); text-align: center; }
  .gallery .section-title { position: absolute; left: 0; width: 1200px; top: 22px; color: var(--ink); }
  .gallery-intro { position: absolute; left: 110px; width: 980px; top: 76px; font-size: 12.5px; line-height: 25px; color: var(--body-text); }
  .gallery-item { position: absolute; top: 151px; width: 320px; }
  .gallery-photo { width: 320px; height: 212px; }
  .gallery-caption { font-family: 'Tinos', serif; font-size: 18px; margin-top: 12px; color: var(--ink); }

  .testimonials { position: absolute; left: 0; top: 1668px; width: 1200px; height: 300px; background: radial-gradient(ellipse at 50% 50%, #3a3a3a 0%, #0c0c0c 80%); color: var(--white); }
  .testimonials .section-title { position: absolute; left: 0; width: 1200px; top: 44px; text-align: center; font-family: 'Open Sans', sans-serif; font-size: 25px; }
  .testimonial-avatar { position: absolute; left: 125px; top: 100px; width: 134px; height: 134px; border-radius: 50%; background: linear-gradient(160deg, #e8e8e8 0%, #b9b2a8 55%, #2a3550 100%); border: 4px solid var(--white); }
  .testimonial-quote { position: absolute; left: 285px; top: 140px; width: 800px; font-family: 'Tinos', serif; font-size: 19px; line-height: 30px; }
  .testimonial-author { position: absolute; right: 118px; top: 241px; font-family: 'Tinos', serif; font-size: 18px; font-weight: 700; }

  .contact { position: absolute; left: 0; top: 1968px; width: 1200px; height: 465px; background: linear-gradient(180deg, var(--contact-a) 0%, var(--contact-b) 55%, #6f93b6 100%); }
  .contact .section-title { position: absolute; left: 0; width: 1200px; top: 26px; text-align: center; color: var(--white); font-family: 'Open Sans', sans-serif; font-size: 25px; }
  .field { position: absolute; left: 100px; width: 402px; background: var(--white); font-size: 13px; color: #9a9a9a; padding: 15px 13px; }
  .submit-btn { position: absolute; left: 100px; top: 379px; width: 402px; height: 45px; border-radius: 4px; background: linear-gradient(180deg, #3a3a3a, #111111); color: var(--white); font-size: 15px; text-align: center; line-height: 45px; }
  .contact-map { position: absolute; left: 562px; top: 99px; width: 538px; height: 325px; background: linear-gradient(135deg, #e6e2d6 0%, #d9d5c8 50%, #efe3a8 100%); border: 2px solid var(--white); }

  .site-footer { position: absolute; left: 0; top: 2433px; width: 1200px; height: 67px; background: var(--footer-bg); }
  .copyright { position: absolute; left: 100px; top: 24px; font-size: 13px; color: var(--white); }
  .social-dot { position: absolute; top: 17px; width: 32px; height: 32px; background: var(--silver); }
</style>
</head>
<body>

<header class="site-nav">
  <span class="nav-link" style="left:155px">Home</span>
  <span class="nav-link" style="left:263px">About Us</span>
  <span class="nav-link" style="left:402px">Diamond Types</span>
  <div class="brand">Lunacrest<br>Gems</div>
  <span class="nav-link" style="left:738px">Gallery</span>
  <span class="nav-link" style="left:860px">Testimonials</span>
  <span class="nav-link" style="left:995px">Contact Us</span>
</header>

<section class="hero" role="img" aria-label="Landscape photograph of forested sandstone cliffs and a valley in New South Wales">
  <h1 class="hero-title" style="font-weight:400">Diamond Engagement Rings &amp; Jewellery</h1>
  <svg class="hero-arrow" style="left:52px" width="20" height="36" viewBox="0 0 20 36"><polyline points="16,4 4,18 16,32" fill="none" stroke="#ffffff" stroke-width="5"/></svg>
  <svg class="hero-arrow" style="left:1123px" width="20" height="36" viewBox="0 0 20 36"><polyline points="4,4 16,18 4,32" fill="none" stroke="#ffffff" stroke-width="5"/></svg>
  <svg class="hero-dots" width="80" height="16" viewBox="0 0 80 16">
    <circle cx="13" cy="8" r="6" fill="#111111" stroke="#ffffff" stroke-width="1.5"/>
    <circle cx="34" cy="8" r="6" fill="#ffffff"/>
    <circle cx="55" cy="8" r="6" fill="#ffffff"/>
  </svg>
</section>

<section class="about">
  <h2 class="section-title">About Us</h2>
  <div class="about-copy">
    <p>At Lunacrest Gems we are passionate about fine jewellery and gems. We feature one of a kind, original and elegant, handmade pieces. Lunacrest Gems handmade jewellery is crafted using exceptional quality metals, integrating designs that are innovative, creative, and unique.</p>
    <p>After you have consulted with our experienced staff - our highly trained and experienced jewellers hand-make every piece of finely crafted jewellery with a level of care and attention that cannot be matched by machines. Our custom jewellery is Australian-made in our Sydney workshop.</p>
    <p>With our combination of one-to-one customer service, our deep knowledge and experience, we can help you create unique jewellery that cannot be found in any jewellery store.</p>
  </div>
  <div class="about-photo" role="img" aria-label="Photograph of a wedding bouquet beside an open box holding a pair of rings"></div>
</section>

<section class="diamond-types">
  <h2 class="section-title">Diamond Types</h2>

  <div class="type-card" style="left:240px">
    <svg class="type-icon" width="82" height="82" viewBox="0 0 82 82">
      <circle cx="41" cy="41" r="39" fill="#111111" stroke="#ffffff" stroke-width="2"/>
      <g fill="none" stroke="#ffffff" stroke-width="2.2" stroke-linejoin="round"><polygon points="29,33 35,26 47,26 53,33 41,55"/><line x1="29" y1="33" x2="53" y2="33"/><polyline points="35,26 38,33 41,55 44,33 47,26"/></g>
    </svg>
    <h3 class="type-name">White Diamonds</h3>
    <p class="type-text">This template was designed specially for you. It's easy to customize anything. Fully responsive layout to customize anything. Fully responsive layout</p>
    <p class="type-more">Read More +</p>
  </div>

  <div class="type-card" style="left:602px">
    <svg class="type-icon" width="82" height="82" viewBox="0 0 82 82">
      <circle cx="41" cy="41" r="39" fill="var(--pink)" stroke="#ffffff" stroke-width="2"/>
      <g fill="none" stroke="#ffffff" stroke-width="2.2" stroke-linejoin="round"><polygon points="29,33 35,26 47,26 53,33 41,55"/><line x1="29" y1="33" x2="53" y2="33"/><polyline points="35,26 38,33 41,55 44,33 47,26"/></g>
    </svg>
    <h3 class="type-name">Pink Diamonds</h3>
    <p class="type-text">This template was designed specially for you. It's easy to customize anything. Fully responsive layout to customize anything. Fully responsive layout</p>
    <p class="type-more">Read More +</p>
  </div>

  <div class="type-card" style="left:947px">
    <svg class="type-icon" width="82" height="82" viewBox="0 0 82 82">
      <circle cx="41" cy="41" r="39" fill="var(--blue)" stroke="#ffffff" stroke-width="2"/>
      <g fill="none" stroke="#ffffff" stroke-width="2.2" stroke-linejoin="round"><polygon points="29,33 35,26 47,26 53,33 41,55"/><line x1="29" y1="33" x2="53" y2="33"/><polyline points="35,26 38,33 41,55 44,33 47,26"/></g>
    </svg>
    <h3 class="type-name">Blue Diamonds</h3>
    <p class="type-text">This template was designed specially for you. It's easy to customize anything. Fully responsive layout to customize anything. Fully responsive layout</p>
    <p class="type-more">Read More +</p>
  </div>
</section>

<section class="gallery">
  <h2 class="section-title">Gallery</h2>
  <p class="gallery-intro">Every project and every client is unique, and so we offer no standard approach. Depending on the brief, we assemble the right mix of services – whether the final output is a strategy, or something that brings strategy to life, such as a new digital project, a fundraising product, a flagship report, or a PR campaign</p>

  <figure class="gallery-item" style="left:98px">
    <div class="gallery-photo" role="img" aria-label="Photograph of loose cut diamonds on a dark surface" style="background:linear-gradient(160deg,#3a3a3a 0%,#9a9a9a 45%,#d6d6d6 60%,#2b2b2b 100%)"></div>
    <figcaption class="gallery-caption">Crisis Christmas parties</figcaption>
  </figure>
  <figure class="gallery-item" style="left:440px">
    <div class="gallery-photo" role="img" aria-label="Photograph of a diamond halo engagement ring on white" style="background:linear-gradient(135deg,#ffffff 0%,#dcdcdc 40%,#9b9b9b 70%,#f2f2f2 100%);border:1px solid #cccccc"></div>
    <figcaption class="gallery-caption">Child-centred development</figcaption>
  </figure>
  <figure class="gallery-item" style="left:780px">
    <div class="gallery-photo" role="img" aria-label="Photograph of a wedding party standing under a stone archway" style="background:linear-gradient(180deg,#6a5a45 0%,#d8d4c8 35%,#3b3b32 70%,#c9b84a 100%)"></div>
    <figcaption class="gallery-caption">A campaign for girls</figcaption>
  </figure>
</section>

<section class="testimonials">
  <h2 class="section-title" style="font-weight:400">Testimonials</h2>
  <div class="testimonial-avatar" role="img" aria-label="Portrait photograph of the reviewer"></div>
  <blockquote class="testimonial-quote">As soon as I saw this theme it was love at first site, I knew I had to somehow get it to notice me, so I did what any good man would do... I used money to buy its affections!</blockquote>
  <p class="testimonial-author">—&nbsp; Dorian Vell</p>
</section>

<section class="contact">
  <h2 class="section-title" style="font-weight:400">Contact Us</h2>
  <div class="field" style="top:99px;height:53px">Your Name</div>
  <div class="field" style="top:170px;height:54px">Your Email</div>
  <div class="field" style="top:242px;height:122px">Message</div>
  <div class="submit-btn">Submit</div>
  <div class="contact-map" role="img" aria-label="Street map showing the workshop location in Sydney"></div>
</section>

<footer class="site-footer">
  <p class="copyright">© 2014 Lunacrest Gems All Rights Reserved</p>
  <span class="social-dot" style="left:917px" aria-label="Social link"></span>
  <span class="social-dot" style="left:967px" aria-label="Social link"></span>
  <span class="social-dot" style="left:1017px" aria-label="Social link"></span>
  <span class="social-dot" style="left:1067px" aria-label="Social link"></span>
</footer>

</body>
</html>
```